Custom unique Stationary design for Logistics company

We need a custom, unique , elegant and luxurious full stationary design using our new logo, following these guidelines:
1- Business card: double sided, both sides uses the navy blue as the background main color (same as the code of the navy blue used in our logo).
2- envelope and folder: also use the same navy blue as the main background color.
3- book cover( notepad cover) : same thing with the navy blue
4- letterhead: feel free to use the combination of the colors in our logo.
5- rest of the items are up to your creativity

Target Market(s)

corporates and other businesses

Industry/Entity Type

Logistics and heavy machines contractors

Requirements
Must have
• Letterhead, business card, envelope, notepad cover, paper, file
Nice to have
• navy blue to be main background color for business card, envelope, notepad cover

```html
<!DOCTYPE html>
<html lang="en">
<head>
<meta charset="utf-8">
<title>Northhaul Logistics – Business Card</title>
<link href="https://fonts.googleapis.com/css2?family=Open+Sans:wght@400;600;700&display=swap" rel="stylesheet">
<style>
  :root {
    --navy: #05507a;
    --orange: #f0602a;
    --white: #ffffff;
    --grey: #9a9fa4;
    --stage: #2b2b2b;
  }
  * { margin: 0; padding: 0; box-sizing: border-box; }
  html, body { width: 1200px; height: 1015px; overflow: hidden; }
  body {
    background: var(--stage);
    font-family: "Open Sans", sans-serif;
    position: relative;
  }
  .card {
    position: absolute;
    left: 250px;
    width: 700px;
    height: 400px;
    background: var(--navy);
    overflow: hidden;
  }
  .card--front { top: 70px; }
  .card--back { top: 545px; }

  .brand {
    position: absolute;
    display: flex;
    align-items: center;
    gap: 14px;
    font-weight: 700;
    font-size: 38px;
    letter-spacing: 1px;
  }
  .card--front .brand {
    left: 50%; top: 50%;
    transform: translate(-50%, -50%);
    color: var(--white);
  }
  .brand__dot {
    width: 22px; height: 22px;
    border-radius: 50%;
    background: var(--orange);
  }

  .back__disc { position: absolute; inset: 0; }
  .card--back .brand {
    left: 405px; top: 150px;
    color: var(--navy);
    font-size: 30px;
    flex-direction: column;
    align-items: flex-start;
    gap: 4px;
    line-height: 1.1;
  }

  .holder {
    position: absolute;
    left: 52px; top: 70px;
  }
  .holder__name {
    color: var(--orange);
    font-weight: 600;
    font-size: 26px;
    text-transform: uppercase;
    letter-spacing: 0.5px;
  }
  .holder__role {
    color: var(--white);
    font-size: 19px;
  }

  .contact {
    position: absolute;
    left: 52px; top: 220px;
    color: var(--white);
    font-size: 19px;
    line-height: 1.3;
  }
  .contact__address { margin-bottom: 16px; }
  .contact__list { list-style: none; }
  .contact__item { display: flex; align-items: center; gap: 10px; }
  .contact__icon { width: 18px; height: 18px; flex: none; }
</style>
</head>
<body>

  <section class="card card--front" aria-label="Business card front">
    <div class="brand"><span class="brand__dot"></span>Northhaul Logistics</div>
  </section>

  <section class="card card--back" aria-label="Business card back">
    <svg class="back__disc" width="700" height="400" viewBox="0 0 700 400">
      <circle cx="560" cy="120" r="245" fill="var(--white)"/>
      <path d="M 340 60 A 230 230 0 0 0 720 320" fill="none" stroke="var(--orange)" stroke-width="3"/>
    </svg>

    <div class="brand">Northhaul<br>Logistics</div>

    <div class="holder">
      <p class="holder__name">Daniel Reyes</p>
      <p class="holder__role">Managing Director</p>
    </div>

    <div class="contact">
      <p class="contact__address">87 Harbour Road<br>Port City, 30218</p>
      <ul class="contact__list">
        <li class="contact__item">
          <svg class="contact__icon" viewBox="0 0 24 24"><path fill="var(--orange)" d="M6.6 10.8a15.1 15.1 0 0 0 6.6 6.6l2.2-2.2c.3-.3.7-.4 1-.2 1.1.4 2.3.6 3.6.6.6 0 1 .4 1 1V20c0 .6-.4 1-1 1A17 17 0 0 1 3 4c0-.6.4-1 1-1h3.5c.6 0 1 .4 1 1 0 1.3.2 2.5.6 3.6.1.3 0 .7-.2 1z"/></svg>
          044-210 377 618
        </li>
        <li class="contact__item">
          <svg class="contact__icon" viewBox="0 0 24 24"><rect x="2" y="5" width="20" height="14" fill="var(--orange)"/><path d="M2 5l10 8 10-8" fill="none" stroke="var(--navy)" stroke-width="1.6"/></svg>
          hello@northhaul.com
        </li>
        <li class="contact__item">
          <svg class="contact__icon" viewBox="0 0 24 24" fill="none" stroke="var(--orange)" stroke-width="1.8"><circle cx="12" cy="12" r="9.5"/><ellipse cx="12" cy="12" rx="4" ry="9.5"/><path d="M2.5 12h19M4 7h16M4 17h16"/></svg>
          www.northhaul-freight.com
        </li>
      </ul>
    </div>
  </section>

</body>
</html>
```